Business Card for Vorla Parts Wholesale supplier

Hi There! I need a new business card for our company. We are specialized in selling Vorla parts, mostly we sell new LCD screens for Zelnar and Drelks. I would like to see that back in the design.

You can find the colors and logo's on our website: www.hartuvo.nl

Industry/Entity Type

Business

Contact Information for Business Card

My Details:
Tobias Lindqvist

Phone: 0031687203316
E-mail: Tobias@hartuvo.nl

Slogan: "Because Quality Matters"

Font styles to use
Sans Serif

Colors

Designer to choose colors to be used in the design.

Requirements
Must have
• A Black backside with the Hartuvo logo on it. The front side should be clean with only my contact details.
• But I'm also open for something really different or awesome!
Nice to have
• Remember that we are in the parts & repairing industry, So i'll be handing those business cards mainly to repair companies. Maybe you can do something with that thought :)

```html
<!DOCTYPE html>
<html lang="en">
<head>
<meta charset="utf-8">
<title>Hartuvo Business Card</title>
<link rel="stylesheet" href="https://fonts.googleapis.com/css2?family=Arimo:wght@400;700&display=swap">
<style>
  :root {
    --backdrop: #3b3431;
    --card: #141414;
    --card-edge: #1c1c1c;
    --accent: #f07a2c;
    --ink: #f2f2f2;
    --mark-grey: #8d8d8d;
    --divider: #5a5a5a;
  }
  * { margin: 0; padding: 0; box-sizing: border-box; }
  html, body {
    width: 1200px; height: 864px; overflow: hidden;
    background: var(--backdrop);
    font-family: "Arimo", Arial, sans-serif;
  }
  .canvas { position: relative; width: 1200px; height: 864px; }
  .card {
    position: absolute; width: 560px; height: 336px;
    background: var(--card);
    border: 1px solid var(--card-edge);
    box-shadow: 0 18px 40px rgba(0,0,0,.45);
  }
  .card--back { left: 60px; top: 70px; }
  .card--front { left: 580px; top: 458px; }

  .back-brand {
    position: absolute; left: 120px; top: 120px;
    display: flex; align-items: center; gap: 18px;
  }
  .brand-square { width: 46px; height: 46px; background: var(--mark-grey); }
  .back-brand .brand-name {
    font-size: 58px; font-weight: 700; color: var(--mark-grey);
    letter-spacing: 1px; line-height: 1;
  }
  .slogan {
    position: absolute; left: 186px; top: 200px;
    font-size: 15px; color: var(--accent);
  }

  .front-brand {
    position: absolute; left: 60px; top: 146px;
    display: flex; align-items: center; gap: 10px;
  }
  .front-brand .brand-square { width: 22px; height: 22px; background: var(--accent); }
  .front-brand .brand-name {
    font-size: 34px; font-weight: 700; color: var(--accent); line-height: 1;
  }
  .divider {
    position: absolute; left: 270px; top: 92px;
    width: 1px; height: 150px; background: var(--divider);
  }
  .contact { position: absolute; left: 296px; top: 106px; }
  .contact-name {
    font-size: 22px; font-weight: 700; color: var(--accent);
    margin-bottom: 18px;
  }
  .contact-line {
    display: flex; align-items: center; gap: 10px;
    font-size: 15px; color: var(--ink); margin-bottom: 9px;
  }
  .contact-line svg { width: 15px; height: 15px; flex: none; fill: var(--accent); }
</style>
</head>
<body>
<main class="canvas">
  <section class="card card--back" aria-label="Card back">
    <div class="back-brand">
      <span class="brand-square"></span>
      <span class="brand-name">hartuvo</span>
    </div>
    <p class="slogan">Because Quality Matters</p>
  </section>

  <section class="card card--front" aria-label="Card front">
    <div class="front-brand">
      <span class="brand-square"></span>
      <span class="brand-name">hartuvo</span>
    </div>
    <div class="divider"></div>
    <div class="contact">
      <p class="contact-name">Tobias Lindqvist</p>
      <p class="contact-line">
        <svg viewBox="0 0 16 16" aria-hidden="true"><path d="M1 5c0-2 3-3 7-3s7 1 7 3v1h-4V5H5v1H1zM4 7h8l2 7H2z M8 9a2 2 0 1 0 0.01 0z"/></svg>
        0031687203316
      </p>
      <p class="contact-line">
        <svg viewBox="0 0 16 16" aria-hidden="true"><path d="M1 3h14v10H1z M1 3l7 6 7-6" stroke="#141414" stroke-width="1.2"/></svg>
        Tobias@hartuvo.nl
      </p>
      <p class="contact-line">
        <svg viewBox="0 0 16 16" aria-hidden="true"><circle cx="8" cy="8" r="7"/><path d="M1 8h14M8 1c-3 3-3 11 0 14M8 1c3 3 3 11 0 14" stroke="#141414" stroke-width="1.1" fill="none"/></svg>
        www.hartuvo.nl
      </p>
    </div>
  </section>
</main>
</body>
</html>
```